GlassHaven Artbook for Okanagan Region, British Columbia

Creating an art book: GlassHaven, for the Okanagan Wine Region in British Columbia, Canada. Would like smart, modern, clean and linear...cool, sexy urban, not ugly boring suburban... I need a cover that appeals to the wino in all of us! Title: GlassHaven -Marla Dovicki
Updates
Thank you all kindly for your efforts. I have added some files so that you can get a sense of my aesthetic...it's never easy trying to figure it out, is it? I will hopefully have dimensions of book soon...cheers, Marla
would anyone please design a giant wine bottle with the wine label that looks like a label but says glasshaven...just curious to see if it works as a design or not...thank you.
Target Market(s)
Designing this wine art book of quotes to wineries in Okanagan BC. Buyer is wine lover and tourist ready to spend his vacation bucks on this wonderful book!
Look and feel

```html
<!DOCTYPE html>
<html lang="en">
<head>
<meta charset="utf-8">
<title>GlassHaven — Book Cover</title>
<link href="https://fonts.googleapis.com/css2?family=Mukta:wght@300;700&display=swap" rel="stylesheet">
<style>
  :root {
    --page: #ffffff;
    --cover-edge: #1a1a1a;
    --wine-red: #ed1f2a;
    --glass-grey: #f1f1ec;
    --author-grey: #555555;
  }
  html, body {
    margin: 0;
    padding: 0;
    width: 1200px;
    height: 1000px;
    overflow: hidden;
    background: var(--page);
  }
  .canvas {
    position: relative;
    width: 1200px;
    height: 1000px;
    background: var(--page);
  }
  .cover {
    position: absolute;
    left: 374px;
    top: 173px;
    width: 470px;
    height: 651px;
    border: 1px solid var(--cover-edge);
    background: var(--page);
  }
  .cover-artwork {
    position: absolute;
    left: 642px;
    top: 251px;
    width: 172px;
    height: 497px;
    border-radius: 6px;
    opacity: 0.9;
    background: linear-gradient(180deg,
      var(--wine-red) 0%,
      var(--wine-red) 55%,
      var(--glass-grey) 70%,
      var(--glass-grey) 100%);
  }
  .title-block {
    position: absolute;
    right: 566px;
    top: 688px;
    text-align: right;
    font-family: "Mukta", sans-serif;
  }
  .author {
    margin: 0 -2.6px 0 0;
    font-weight: 300;
    font-size: 15px;
    line-height: 28px;
    letter-spacing: 2.6px;
    color: var(--author-grey);
  }
  .title {
    margin: 2px -3px 0 0;
    font-weight: 700;
    font-size: 33px;
    line-height: 40px;
    letter-spacing: 3px;
    color: var(--wine-red);
  }
</style>
</head>
<body>
  <div class="canvas">
    <div class="cover"></div>
    <div class="cover-artwork" role="img" aria-label="Illustration of a red wine glass hanging upside down, overlapping a pale upright wine glass"></div>
    <div class="title-block">
      <p class="author">MARLA DOVICKI</p>
      <h1 class="title">GLASSHAVEN</h1>
    </div>
  </div>
</body>
</html>
```